Rollway Stays

We are 100% online, promoting accommodation details and booking facilities for wheelchair dependant travellers.
Listings will only be accommodation providers which meet our specific criteria.

Target Market(s)

Wheelchair dependant people and their companions

Industry/Entity Type

Accommodation

Contact Information for Business Card

Name, mobile phone number, email address, website address

```html
<!DOCTYPE html>
<html lang="en">
<head>
<meta charset="utf-8">
<title>Rollway Stays — Business Card</title>
<link rel="stylesheet" href="https://fonts.googleapis.com/css2?family=Michroma&family=Oswald:wght@500&family=Roboto:wght@400;500&display=swap">
<style>
  :root {
    --brand-blue: #00aeef;
    --card-white: #ffffff;
    --rule-grey: #8a8a8a;
    --ink-dark: #2b2b2b;
    --backdrop: #e6e7e9;
  }
  * { box-sizing: border-box; margin: 0; padding: 0; }
  html, body { width: 1200px; height: 933px; overflow: hidden; }
  body {
    background: var(--backdrop);
    font-family: "Roboto", Arial, sans-serif;
    position: relative;
  }
  .card {
    position: absolute;
    left: 260px;
    width: 680px;
    height: 388px;
    background: var(--card-white);
    box-shadow: 0 6px 18px rgba(0,0,0,0.12);
    overflow: hidden;
  }
  .card--front { top: 40px; }
  .card--back { top: 505px; }

  .brand-square {
    position: absolute;
    left: 136px;
    top: 0;
    width: 166px;
    height: 164px;
    background: var(--brand-blue);
  }
  .brand-name {
    position: absolute;
    font-family: "Michroma", "Arial", sans-serif;
    color: var(--brand-blue);
    white-space: nowrap;
    letter-spacing: 1px;
  }
  .card--front .brand-name { left: 300px; top: 176px; font-size: 30px; }
  .card--back .brand-name { left: 268px; top: 118px; font-size: 28px; }

  .contact-panel {
    position: absolute;
    left: 34px;
    top: 58px;
    width: 196px;
    height: 196px;
    background: var(--brand-blue);
    color: var(--card-white);
    padding: 16px 14px;
    font-size: 11.5px;
    line-height: 1.45;
  }
  .contact-address { margin-bottom: 12px; }
  .contact-list { list-style: none; }
  .contact-list li {
    display: flex;
    align-items: center;
    gap: 7px;
    height: 19px;
  }
  .contact-list svg { width: 11px; height: 11px; flex: none; fill: var(--card-white); }

  .divider {
    position: absolute;
    left: 230px;
    right: 10px;
    top: 174px;
    height: 4px;
    background: var(--rule-grey);
  }
  .holder {
    position: absolute;
    left: 246px;
    top: 196px;
  }
  .holder-name {
    font-family: "Oswald", "Arial Narrow", sans-serif;
    font-weight: 500;
    font-size: 30px;
    color: var(--brand-blue);
    letter-spacing: 0.5px;
    line-height: 1.1;
  }
  .holder-title {
    font-family: "Roboto", Arial, sans-serif;
    font-weight: 500;
    font-size: 15px;
    color: var(--ink-dark);
    letter-spacing: 1px;
  }
</style>
</head>
<body>

<section class="card card--front" aria-label="Business card front">
  <div class="brand-square"></div>
  <div class="brand-name">Rollway Stays</div>
</section>

<section class="card card--back" aria-label="Business card back">
  <div class="contact-panel">
    <p class="contact-address">42 Harbour Lane<br>Level 2 North Wing</p>
    <ul class="contact-list">
      <li><svg viewBox="0 0 12 12"><path d="M2.5 1h2l1 2.5-1.2 1a6 6 0 0 0 3.2 3.2l1-1.2 2.5 1v2a1 1 0 0 1-1 1A9 9 0 0 1 1.5 2a1 1 0 0 1 1-1z"/></svg>020 555 0147</li>
      <li><svg viewBox="0 0 12 12"><path d="M3.5 0.5h5a1 1 0 0 1 1 1v9a1 1 0 0 1-1 1h-5a1 1 0 0 1-1-1v-9a1 1 0 0 1 1-1zm0.5 1.5v7h4v-7zm2 8a0.6 0.6 0 1 0 0 .01z"/></svg>020 555 0192</li>
      <li><svg viewBox="0 0 12 12"><path d="M1 3h10v7H1zm1 1v5h8V4zm1-2.5h6V3H3z"/></svg>020 555 0168</li>
      <li><svg viewBox="0 0 12 12"><path d="M1 2.5h10v7H1zm1 1.2v.3l4 2.6 4-2.6v-.3z"/></svg>hello@rollwaystays.com</li>
      <li><svg viewBox="0 0 12 12"><path d="M6 0.5a5.5 5.5 0 1 0 0 11 5.5 5.5 0 0 0 0-11zm0 1.2c.8.9 1.3 2.3 1.4 3.7H4.6C4.7 4 5.2 2.6 6 1.7zM1.8 6.6h1.8c.1 1.3.5 2.5 1.1 3.5a4.3 4.3 0 0 1-2.9-3.5zm0-1.2a4.3 4.3 0 0 1 2.9-3.5c-.6 1-1 2.2-1.1 3.5zm4.2 4.9c-.8-.9-1.3-2.3-1.4-3.7h2.8c-.1 1.4-.6 2.8-1.4 3.7zm1.3-.2c.6-1 1-2.2 1.1-3.5h1.8a4.3 4.3 0 0 1-2.9 3.5zm1.1-4.7c-.1-1.3-.5-2.5-1.1-3.5a4.3 4.3 0 0 1 2.9 3.5z"/></svg>www.rollwaystays.com</li>
    </ul>
  </div>
  <div class="brand-name">Rollway Stays</div>
  <div class="divider"></div>
  <div class="holder">
    <p class="holder-name">DANIEL MARSH</p>
    <p class="holder-title">GENERAL MANAGER</p>
  </div>
</section>

</body>
</html>
```